RW Framewell Inc Business cards

We need business cards using our existing logo but slightly modified. Right now the logo says RW Loadbearing Masonry. We want to keep the RW part of the design, but replace the Structural Concrete portion with "FRAMEWELL". Please see the attached file.
Ideally this would be a blank template so we can add Different Names, titles, and phone numbers later.
On the one side we want only the logo and on the other side the detail. I'm attaching an example for you to see.
Please reach out with any other questions. Our address and other details will be given out once we find a design we like.

Target Market(s)

Construction Industry

```html
<!DOCTYPE html>
<html lang="en">
<head>
<meta charset="UTF-8">
<title>RW Framewell Inc – Business Cards</title>
<link href="https://fonts.googleapis.com/css2?family=Montserrat:wght@600&family=Roboto:wght@400;500&display=swap" rel="stylesheet">
<style>
  :root {
    --backdrop: #5a5a5a;
    --card: #1f1f21;
    --brand-blue: #2f6bbd;
    --logo-grey: #8c8c8e;
    --text-light: #f2f2f2;
  }
  * { margin: 0; padding: 0; box-sizing: border-box; }
  html, body {
    width: 799px; height: 1200px; overflow: hidden;
    background: var(--backdrop);
  }
  .sheet {
    position: relative; width: 799px; height: 1200px;
    display: flex; flex-direction: column; align-items: center;
    justify-content: space-around; padding: 60px 0;
  }
  .card {
    width: 620px; height: 354px;
    background: var(--card);
    border-radius: 4px;
    box-shadow: 0 10px 24px rgba(0,0,0,0.35);
    position: relative;
    overflow: hidden;
  }
  .card--front {
    display: flex; align-items: center; justify-content: center;
  }
  .wordmark {
    font-family: 'Montserrat', sans-serif;
    font-weight: 600;
    letter-spacing: 4px;
    white-space: nowrap;
  }
  .card--front .wordmark { font-size: 44px; color: var(--logo-grey); }
  .card--back .wordmark {
    position: absolute; left: 36px; top: 150px;
    width: 300px;
    font-size: 23px; letter-spacing: 3px; color: var(--text-light);
    display: flex; align-items: center; gap: 10px;
  }
  .wordmark-square {
    width: 16px; height: 16px; background: var(--brand-blue); display: inline-block; flex: none;
  }
  .details {
    position: absolute; left: 372px; top: 92px; width: 230px;
    font-family: 'Roboto', sans-serif; color: var(--text-light);
  }
  .details__name { font-size: 21px; font-weight: 500; color: var(--brand-blue); }
  .details__title { font-size: 15px; margin-bottom: 20px; }
  .contact-list { list-style: none; font-size: 16px; line-height: 25px; }
  .contact-list li { display: flex; align-items: center; gap: 12px; white-space: nowrap; }
  .contact-list svg { width: 14px; height: 14px; fill: var(--brand-blue); flex: none; }
  .details__address { font-size: 16px; line-height: 22px; margin-top: 4px; }
</style>
</head>
<body>
<main class="sheet">
  <section class="card card--front" aria-label="Card front">
    <span class="wordmark">RW FRAMEWELL</span>
  </section>

  <section class="card card--back" aria-label="Card back">
    <div class="wordmark"><span class="wordmark-square"></span>RW FRAMEWELL</div>
    <div class="details">
      <p class="details__name">Alex RW Moreno</p>
      <p class="details__title">Managing Director</p>
      <ul class="contact-list">
        <li>
          <svg viewBox="0 0 24 24" aria-hidden="true"><path d="M6.6 10.8a15.1 15.1 0 0 0 6.6 6.6l2.2-2.2a1 1 0 0 1 1-.25 11.4 11.4 0 0 0 3.6.57 1 1 0 0 1 1 1V20a1 1 0 0 1-1 1A17 17 0 0 1 3 4a1 1 0 0 1 1-1h3.5a1 1 0 0 1 1 1c0 1.250.2 2.45.57 3.57a1 1 0 0 1-.25 1z"/></svg>
          555-014-2087
        </li>
        <li>
          <svg viewBox="0 0 24 24" aria-hidden="true"><path d="M2 5h20v14H2z M2 5l10 8 10-8" stroke="#1f1f21" stroke-width="1.5"/></svg>
          alex@yoursitename.com
        </li>
        <li>
          <svg viewBox="0 0 24 24" aria-hidden="true"><circle cx="12" cy="12" r="10"/><path d="M2 12h20M12 2c3 3 3 17 0 20M12 2c-3 3-3 17 0 20" stroke="#1f1f21" stroke-width="1.5" fill="none"/></svg>
          www.yoursitename.com
        </li>
      </ul>
      <p class="details__address">418 Sample Ave., Some Town,<br>Oregon, US 654321</p>
    </div>
  </section>
</main>
</body>
</html>
```